I need a business card to give to prospective clients. I am a freelance photographer who photographs most things (except weddings and social stuff) including nature, wildlife and interiors.
I want to look modern and stylish.
I am including a photograph although I am by no means certain that it should be used - what do you think?
More of my images can be seen and downloaded at my PixVault page - just search for Maren Tolbeck
Target Market(s)
Home owners selling or letting properties, private individuals wanting to buy prints
Industry/Entity Type
Business
Contact Information for Business Card
Maren Tolbeck Photography
Maren
Wrenfield Cottage, Mossbank Road, Pelsworth, Carrow Heath, KX41 2RB
Tel: +44 7000 418263. Email: maren@tolbeckstudio.example

```html
<!DOCTYPE html>
<html lang="en">
<head>
<meta charset="utf-8">
<title>Maren Tolbeck Photography — Business Card</title>
<link rel="stylesheet" href="https://fonts.googleapis.com/css2?family=Fondamento&family=Alegreya:wght@400&display=swap">
<style>
  :root {
    --page-bg: #ffffff;
    --card-green: #7b973a;
    --card-green-light: #8fa94a;
    --card-green-dark: #6d8a30;
    --title-crimson: #a3163f;
    --contact-cream: #f3f1e2;
    --name-green: #3e6a2c;
    --lens-dark: #1c2418;
    --lens-mid: #3b4a33;
    --lens-glow: #5f8a4a;
    --haze-yellow: #b8c35a;
  }
  * { margin: 0; padding: 0; box-sizing: border-box; }
  html, body {
    width: 1200px;
    height: 1000px;
    overflow: hidden;
    background: var(--page-bg);
  }
  .sheet {
    position: relative;
    width: 1200px;
    height: 1000px;
  }
  .card {
    position: absolute;
    width: 690px;
    height: 405px;
    overflow: hidden;
  }

  /* Front of card */
  .card--front {
    left: 80px;
    top: 40px;
    background:
      radial-gradient(ellipse at 30% 40%, var(--card-green-light) 0%, transparent 60%),
      linear-gradient(180deg, var(--card-green) 0%, var(--card-green-dark) 100%);
  }
  .card__lens-photo {
    position: absolute;
    left: 410px;
    top: -30px;
    width: 460px;
    height: 460px;
    background:
      radial-gradient(circle closest-side at 50% 50%,
        var(--lens-glow) 0%,
        var(--lens-mid) 30%,
        var(--lens-dark) 62%,
        rgba(28, 36, 24, 0.6) 82%,
        rgba(28, 36, 24, 0) 100%);
  }
  .card__title {
    position: absolute;
    left: 48px;
    top: 62px;
    font-family: "Fondamento", cursive;
    font-size: 30px;
    font-weight: 400;
    letter-spacing: 0.3px;
    color: var(--title-crimson);
    white-space: nowrap;
  }
  .card__address,
  .card__contact {
    position: absolute;
    font-family: "Alegreya", serif;
    font-size: 19px;
    color: var(--contact-cream);
    font-style: normal;
  }
  .card__address { left: 48px; top: 158px; line-height: 33.5px; }
  .card__contact { left: 28px; top: 325px; line-height: 32px; }

  /* Back of card */
  .card--back {
    left: 435px;
    top: 520px;
    background:
      radial-gradient(ellipse at 38% 10%, var(--haze-yellow) 0%, transparent 45%),
      linear-gradient(160deg, var(--card-green-light) 0%, var(--card-green) 60%, var(--card-green-dark) 100%);
  }
  .card__flower-photo {
    position: absolute;
    left: 0;
    top: 0;
    width: 270px;
    height: 405px;
    background:
      radial-gradient(ellipse 60px 140px at 42% 48%, rgba(201, 58, 126, 0.55) 0%, transparent 100%);
  }
  .card__name {
    position: absolute;
    right: 78px;
    top: 290px;
    font-family: "Fondamento", cursive;
    font-size: 46px;
    color: var(--name-green);
    white-space: nowrap;
  }
</style>
</head>
<body>
  <main class="sheet">
    <section class="card card--front" aria-label="Business card front">
      <div class="card__lens-photo" role="img" aria-label="Close-up photograph of a camera lens"></div>
      <h1 class="card__title">Maren Tolbeck Photography</h1>
      <address class="card__address">
        Wrenfield Cottage,<br>
        Mossbank Road,<br>
        Pelsworth, Carrow Heath,<br>
        KX41 2RB
      </address>
      <p class="card__contact">
        +44 7000 418263.<br>
        maren@tolbeckstudio.example
      </p>
    </section>

    <section class="card card--back" aria-label="Business card back">
      <div class="card__flower-photo" role="img" aria-label="Photograph of a pink wild gladiolus against soft green grass"></div>
      <p class="card__name">Maren Tolbeck</p>
    </section>
  </main>
</body>
</html>
```